I need a flyer made , the flyer can be one page or two pages or three pages . I will be posting this on Instagram and social media platforms. I am a luxury home builder , I am looking to hire a construction project manager . Below are some examples and ideas what can be on the flyer

We’re looking for a construction project manager who’s passionate about building luxury homes at the highest standards
We’re hiring construction project manager
* Experience 5+ years in residential project management with a strong portfolio of completed homes.
* location : Bergen County NJ
* excellent leadership skills, leads teams with confidence and clarity
* communicates seamlessly with architects , engineers, designers and clients
*knows how to manage budgets and timelines without compromising quality
*solves problems with a positive solution first mindset
* pays attention to every detail because in luxury the small things are the big things

Apply now , link in bio or DM to connect.

My logo is attached, my web site www.velstridebuilders.com
My style is modern but still warm and inviting. I like a clean classy look .

Please don’t add any images of chairs or people to the flyer , I do not want people on my flyer. Do not add standard images of offices and houses , we are luxury builders , we build homes over 2 million dollars. Keep a classy , simple modern look . High end .

You can add a white hard hat with my logo on it for a image , this is a suggestion does not have to be on my flyer ,

```html
<!DOCTYPE html>
<html lang="en">
<head>
<meta charset="utf-8">
<title>We're Hiring – Construction Project Manager</title>
<link href="https://fonts.googleapis.com/css2?family=Poppins:wght@300;400;500;600;700;800;900&family=Great+Vibes&display=swap" rel="stylesheet">
<style>
  :root{
    --ink:#0c0c0c;
    --paper:#f4f4f4;
    --paper-shade:#e2e2e2;
    --graphite:#3a3a3a;
    --panel-dark:#050505;
    --panel-mid:#2e2e2e;
    --panel-light:#4a4a4a;
    --text-light:#f2f2f2;
    --line:#8a8a8a;
  }
  *{margin:0;padding:0;box-sizing:border-box}
  html,body{width:1200px;height:1200px;overflow:hidden}
  body{font-family:'Poppins',sans-serif;color:var(--ink);background:var(--paper)}
  .flyer{
    position:relative;width:1200px;height:1200px;overflow:hidden;
    background:
      radial-gradient(ellipse at 80% 15%, #ffffff 0%, rgba(255,255,255,0) 55%),
      linear-gradient(155deg, #fafafa 0%, var(--paper) 45%, var(--paper-shade) 70%, #f7f7f7 100%);
  }
  .skyline-art{
    position:absolute;left:0;top:27px;width:520px;height:630px;
    background:linear-gradient(170deg, rgba(200,200,200,.55) 0%, rgba(225,225,225,.35) 55%, rgba(244,244,244,0) 100%);
    clip-path:polygon(0 8%,40% 0,70% 20%,100% 45%,100% 100%,0 100%);
  }
  .portrait-art{
    position:absolute;left:262px;top:84px;width:222px;height:482px;
    background:linear-gradient(180deg,#e8c23a 0%,#e8c23a 7%,#2a2e3a 12%,#1c2030 60%,#9a7a55 85%,#2a2a2a 100%);
    border-radius:60px 60px 12px 12px;opacity:.9;
  }
  .megaphone-art{
    position:absolute;left:830px;top:86px;width:136px;height:150px;
    background:radial-gradient(circle at 60% 40%,#9a9a9a 0%,#4a4a4a 60%,rgba(74,74,74,0) 72%);
    border-radius:50%;
  }
  .location-pin{position:absolute;left:120px;top:306px;width:168px;height:256px}
  .location-pin .pin-label{
    position:absolute;left:44px;top:44px;width:80px;height:80px;
    display:flex;align-items:center;justify-content:center;text-align:center;
    font-weight:700;font-size:16px;line-height:1.15;color:var(--ink);
  }
  .headline-script{
    position:absolute;left:504px;top:150px;
    font-family:'Great Vibes',cursive;font-weight:400;font-size:118px;line-height:1;color:var(--ink);
  }
  .headline-main{
    position:absolute;left:496px;top:240px;
    font-weight:800;font-size:176px;line-height:1;letter-spacing:-5px;color:var(--ink);
  }
  .role-title{position:absolute;left:500px;top:404px;line-height:1}
  .role-title .line-one{display:block;font-weight:800;font-size:50px;letter-spacing:-.5px}
  .role-title .line-two{display:block;font-weight:300;font-size:43px;margin-top:6px;letter-spacing:-.5px}
  .role-title .line-two strong{font-weight:800}
  .tagline{position:absolute;left:500px;top:526px;display:flex;height:46px}
  .tagline span{
    display:flex;align-items:center;justify-content:center;
    color:var(--text-light);font-size:20px;font-weight:400;
  }
  .tagline span strong{font-weight:700;margin-left:6px}
  .tagline .tag-build{background:var(--panel-dark);border-radius:23px 0 0 23px;width:202px}
  .tagline .tag-lead{background:var(--graphite);border-radius:0 23px 23px 0;width:206px;margin-left:3px}
  .requirements{
    position:absolute;left:77px;top:651px;width:1048px;height:288px;
    border-radius:26px;overflow:hidden;display:flex;
    box-shadow:0 10px 24px rgba(0,0,0,.18);
  }
  .requirements .column{flex:1;padding:34px 64px 0 44px;color:var(--text-light)}
  .requirements .column-left{background:var(--panel-dark)}
  .requirements .column-right{background:linear-gradient(90deg,var(--panel-mid) 0%,var(--panel-light) 60%,var(--panel-mid) 100%);padding:34px 130px 0 16px}
  .requirements ul{list-style:none}
  .requirements li{display:flex;gap:11px;font-size:19px;line-height:24px;font-weight:400;margin-bottom:14px}
  .requirements li strong{font-weight:600}
  .requirements .tick{flex:0 0 15px;margin-top:5px}
  .brand-name{
    position:absolute;left:68px;top:1030px;width:330px;
    font-weight:400;color:var(--ink);
    font-size:42px;line-height:1.05;letter-spacing:4px;text-align:center;
  }
  .brand-name .brand-sub{display:block;font-size:26px;letter-spacing:8px;margin-top:6px}
  .cta{position:absolute;left:432px;top:1008px;display:flex;align-items:center}
  .cta .apply{
    background:var(--ink);color:#fff;font-weight:700;font-size:24px;
    height:49px;width:206px;border-radius:25px;display:flex;align-items:center;justify-content:center;position:relative;z-index:1;
  }
  .cta .connect{
    height:52px;width:422px;margin-left:-6px;border:1.5px solid #9a9a9a;border-radius:26px;background:#fbfbfb;
    display:flex;align-items:center;justify-content:center;font-weight:600;font-size:24px;
  }
  .follow{position:absolute;left:432px;top:1070px}
  .follow h3,.visit h3{font-size:21px;font-weight:700;line-height:1.2}
  .follow .handles{display:flex;gap:16px;margin-top:4px;font-size:19px;font-weight:400}
  .follow .handles span{display:flex;align-items:center;gap:6px}
  .follow .dot{width:11px;height:11px;border-radius:50%;background:var(--ink)}
  .divider{position:absolute;left:823px;top:1078px;width:1px;height:58px;background:var(--line)}
  .visit{position:absolute;left:836px;top:1070px}
  .visit p{font-size:19px;margin-top:4px}
</style>
</head>
<body>
<main class="flyer">
  <div class="skyline-art" role="img" aria-label="Faint wireframe sketch of high-rise buildings"></div>

  <div class="portrait-art" role="img" aria-label="Businessman in suit and yellow hard hat seated on a white chair"></div>

  <div class="location-pin">
    <svg width="168" height="256" viewBox="0 0 168 256" aria-hidden="true">
      <defs>
        <linearGradient id="pinFill" x1="0" y1="0" x2="1" y2="1">
          <stop offset="0" stop-color="#f24a4e"/>
          <stop offset=".6" stop-color="#e3262b"/>
          <stop offset="1" stop-color="#a8151a"/>
        </linearGradient>
      </defs>
      <ellipse cx="96" cy="246" rx="40" ry="8" fill="rgba(0,0,0,.18)"/>
      <path d="M84 4C38 4 4 38 4 82c0 58 70 118 88 164 14-46 72-104 72-164C164 38 130 4 84 4z" fill="url(#pinFill)"/>
      <circle cx="84" cy="84" r="50" fill="#ffffff"/>
    </svg>
    <div class="pin-label">Bergen County, NJ</div>
  </div>

  <h1 class="headline-script">We’re</h1>
  <div class="megaphone-art" role="img" aria-label="Silver megaphone"></div>
  <h2 class="headline-main">HIRING</h2>

  <p class="role-title">
    <span class="line-one">CONSTRUCTION</span>
    <span class="line-two">PROJECT <strong>MANAGER</strong></span>
  </p>

  <div class="tagline">
    <span class="tag-build">BUILD<strong>LUXURY</strong></span>
    <span class="tag-lead">LEAD<strong>EXCELLENCE</strong></span>
  </div>

  <section class="requirements">
    <div class="column column-left">
      <ul>
        <li><svg class="tick" width="15" height="15" viewBox="0 0 17 17"><circle cx="8.5" cy="8.5" r="8.5" fill="#e6e6e6"/><path d="M4.5 8.8l2.6 2.5 5.4-5.4" stroke="#111" stroke-width="2" fill="none"/></svg><span>Experience <strong>5+ years</strong> in residential project management with a strong portfolio of completed homes.</span></li>
        <li><svg class="tick" width="15" height="15" viewBox="0 0 17 17"><circle cx="8.5" cy="8.5" r="8.5" fill="#e6e6e6"/><path d="M4.5 8.8l2.6 2.5 5.4-5.4" stroke="#111" stroke-width="2" fill="none"/></svg><span>Excellent <strong>leadership skills</strong>, leads teams with confidence and clarity</span></li>
        <li><svg class="tick" width="15" height="15" viewBox="0 0 17 17"><circle cx="8.5" cy="8.5" r="8.5" fill="#e6e6e6"/><path d="M4.5 8.8l2.6 2.5 5.4-5.4" stroke="#111" stroke-width="2" fill="none"/></svg><span><strong>Communicates seamlessly</strong> with architects , engineers, designers and clients</span></li>
      </ul>
    </div>
    <div class="column column-right">
      <ul>
        <li><svg class="tick" width="15" height="15" viewBox="0 0 17 17"><circle cx="8.5" cy="8.5" r="8.5" fill="#e6e6e6"/><path d="M4.5 8.8l2.6 2.5 5.4-5.4" stroke="#111" stroke-width="2" fill="none"/></svg><span>Knows how to <strong>manage budgets and timelines</strong> without compromising quality</span></li>
        <li><svg class="tick" width="15" height="15" viewBox="0 0 17 17"><circle cx="8.5" cy="8.5" r="8.5" fill="#e6e6e6"/><path d="M4.5 8.8l2.6 2.5 5.4-5.4" stroke="#111" stroke-width="2" fill="none"/></svg><span><strong>Solves problems</strong> with a positive solution first mindset</span></li>
        <li><svg class="tick" width="15" height="15" viewBox="0 0 17 17"><circle cx="8.5" cy="8.5" r="8.5" fill="#e6e6e6"/><path d="M4.5 8.8l2.6 2.5 5.4-5.4" stroke="#111" stroke-width="2" fill="none"/></svg><span><strong>Pays attention to every detail</strong> because in luxury the small things are the big things</span></li>
      </ul>
    </div>
  </section>

  <div class="brand-name">VELSTRIDE<span class="brand-sub">BUILDERS</span></div>

  <div class="cta">
    <span class="apply">Apply now</span>
    <span class="connect">Link in bio or DM to connect</span>
  </div>

  <div class="follow">
    <h3>Follow us</h3>
    <div class="handles">
      <span><i class="dot"></i>velstridebuilders</span>
      <span><i class="dot"></i>VelstrideHomes</span>
    </div>
  </div>
  <div class="divider"></div>
  <div class="visit">
    <h3>Visit us</h3>
    <p>www.velstridebuilders.com</p>
  </div>
</main>
</body>
</html>
```